Catalogue Design Project

We need a catalog design for a new private university called Redwell Institute Bayshore (see website www.rwi-bs.org). The catalog should be about 30 pages maximum and will include items such as General Information, Academic schedule, department descriptions, program descriptions, course descriptions, school policies, student services, admissions, San diego Lifestyle, etc.
I will provide the text but I need a professional design with regard to page layouts. I have provided some examples.
Ok, i posted the catalog content, just missing course descriptions.
Target Market(s)
Young Professionals, Foreign Students
Industry/Entity Type
University
Look and feel
Each slider illustrates characteristics of the customer's brand and the style your logo design should communicate.

```html
<!DOCTYPE html>
<html lang="en">
<head>
<meta charset="utf-8">
<title>Master of Business Administration (MBA) Degree – Redwell Institute</title>
<link href="https://fonts.googleapis.com/css2?family=Carlito:ital,wght@0,400;0,700;1,400&display=swap" rel="stylesheet">
<style>
  :root {
    --ink: #111111;
    --brand-blue: #2f6596;
    --brand-blue-dark: #24507a;
    --rule: #9fb3c6;
    --muted: #8a8a8a;
    --paper: #ffffff;
    --photo-light: #efe7da;
    --photo-mid: #c9b797;
    --mark-tone: #b4b9c0;
  }
  * { margin: 0; padding: 0; box-sizing: border-box; }
  html, body { width: 927px; height: 1200px; overflow: hidden; background: var(--paper); }
  body { font-family: "Carlito", "Calibri", sans-serif; color: var(--ink); }
  .page { position: relative; width: 927px; height: 1200px; background: var(--paper); }

  .masthead-photo {
    position: absolute; left: 420px; top: 0; width: 507px; height: 104px;
    background: linear-gradient(90deg, rgba(255,255,255,1) 0%, rgba(239,231,218,0.7) 35%, var(--photo-mid) 75%, #b8a27e 100%);
  }
  .masthead-mark {
    position: absolute; left: 58px; top: 36px; width: 150px; height: 36px;
    background: var(--mark-tone); border-radius: 4px;
  }
  .masthead-rule { position: absolute; left: 0; top: 104px; width: 927px; height: 2px; background: var(--rule); }
  .section-tab {
    position: absolute; right: 0; top: 106px; width: 330px; height: 38px;
    background: linear-gradient(90deg, var(--brand-blue-dark), var(--brand-blue));
    clip-path: polygon(18px 0, 100% 0, 100% 100%, 0 100%);
    color: #fff; font-size: 33.5px; line-height: 38px; padding-left: 30px; letter-spacing: 0.3px; white-space: nowrap;
  }

  .content { position: absolute; left: 80px; top: 186px; width: 804px; font-size: 21px; line-height: 25.8px; }
  .program-title { text-align: center; font-size: 27.4px; font-weight: 700; line-height: 30px; margin-bottom: 1px; }
  .content p { text-align: justify; }
  .fact b { font-weight: 700; }
  .label-strong { font-weight: 700; text-decoration: underline; }
  .label { text-decoration: underline; margin-top: 25.8px; }
  .course-grid { display: grid; grid-template-columns: 380px 1fr; }
  .course-grid span { white-space: nowrap; }

  .footer-rule { position: absolute; left: 0; top: 1155px; width: 927px; height: 2px; background: var(--rule); }
  .folio { position: absolute; right: 36px; top: 1167px; font-size: 16.5px; color: var(--muted); letter-spacing: 0.4px; }
</style>
</head>
<body>
<div class="page">
  <div class="masthead-photo" role="img" aria-label="Photograph of open book pages fading into white"></div>
  <div class="masthead-mark" role="img" aria-label="Decorative brand ornament"></div>
  <div class="masthead-rule"></div>
  <div class="section-tab">GRADUATE DEGREE</div>

  <main class="content">
    <h1 class="program-title">Master of Business Administration (MBA) Degree</h1>
    <p>Redwell Institute's MBA program is designed to be flexible, cutting-edge and career minded. It is appropriate for all students with an undergraduate degree, whether in business or other industry area. The coursework not only prepares students for working in upper managerial positions, but also provides valuable knowledge and life tools useful for any profession.</p>
    <p>The program, while rigorous with a technical focus, exposes students to the environmental, social, political, and global economic conditions that produce the international market. The primary advantages of the MBA program at RWIB include small classroom sizes with ample opportunities for interaction with faculty through consultation and individual progress checks, and with classmates through group cooperation on projects in and outside of the classroom. In this manner and with a truly innovative system that keeps students up-to-date with market trends, RWIB creates a real business environment that's unlike any other MBA program.</p>
    <div class="fact"><b>Hours:</b> 6 hours per week</div>
    <div class="fact"><b>Length:</b> 8 weeks per course</div>
    <div class="label-strong">Requirements:</div>
    <div>Bachelor Degree (with passing Calculus score)</div>

    <div class="label">Required Courses:</div>
    <div class="course-grid">
      <span>ACCT 600 Financial Accounting</span><span>ACCT 601 Managerial Accounting</span>
      <span>MKT 601 Marketing Principles</span><span>BUS 601 Statistics</span>
      <span>COMP 603 Information Technology</span><span>BUS 603 Human Resources Management</span>
      <span>BUS 604 Introduction to Finance</span><span>BUS 605 Economic Fundamentals</span>
    </div>

    <div class="label">Elective Courses: (Choose 3)</div>
    <div class="course-grid">
      <span>BUS 600 Starting Your Own Business</span><span>MKT 602 Marketing Research</span>
      <span>MKT 607/ACCT 607 Internship</span><span>MKT 606 E-Commerce</span>
      <span>ACCT 605 Introduction to Investments</span><span>BUS 602 Fundamentals of Importing &amp; Exporting</span>
    </div>

    <div class="label">Learning Outcome:</div>
    <p>Highlights of the MBA program include a real-world business project with a company abroad, design of a professional and working business plan for investors, creation and maintenance of a career-management portfolio. To be sure, this a serious program that prepares graduates to be leaders of their industries, to think with a global perspective, use extensive research, and put their practices into action.</p>
  </main>

  <div class="footer-rule"></div>
  <div class="folio">15::: REDWELL INSTITUTE</div>
</div>
</body>
</html>
```